Automotive eCommerce Business looking for a business card design

Looking for a clean and simple business card design. Our company name is "Brindle Auto" and we are a company specializing in the ecommerce sales of automotive parts, specifically for pick up trucks and large SUVs. Our company colours are red, black, and white.

Feel free to use the logo provided or create a new logo that you seem fit. Looking forward to your creative ideas!

Industry/Entity Type

Automotive

Contact Information for Business Card

We were thinking of a possibly two-sided design featuring just the logo and company name on one side, and personal information on the other side. Single sided designs will be considered as well.

Font styles to use
Serif
Sans Serif
Decorative

Colors
ec1f27
ffffff
000000

Requirements
Must have
• Space for employee's name, title, phone number and email address, along with the company address and website somewhere.

```html
<!DOCTYPE html>
<html lang="en">
<head>
<meta charset="utf-8">
<title>Brindle Auto Ltd. – Business Card</title>
<link rel="stylesheet" href="https://fonts.googleapis.com/css2?family=Roboto:wght@400;500&display=swap">
<style>
  :root {
    --backdrop: #2a2a2a;
    --card: #f2f2f2;
    --brand-red: #961c20;
    --ink: #4a4a4a;
    --ink-soft: #555555;
  }
  * { box-sizing: border-box; margin: 0; padding: 0; }
  html, body {
    width: 1200px; height: 960px; overflow: hidden;
    background: var(--backdrop);
    font-family: "Roboto", Arial, sans-serif;
  }
  .canvas { position: relative; width: 1200px; height: 960px; }
  .card {
    position: absolute; width: 600px; height: 343px;
    background: var(--card); overflow: hidden;
  }
  .card--front { left: 314px; top: 113px; }
  .card--back { left: 311px; top: 472px; }

  .front__band {
    position: absolute; left: 0; top: 0; width: 180px; height: 100%;
    background: var(--brand-red);
  }
  .front__details {
    position: absolute; right: 40px; top: 44px;
    text-align: right; color: var(--ink);
  }
  .company-name {
    font-size: 22px; font-weight: 500; color: var(--ink);
    letter-spacing: 0.5px;
  }
  .person__name {
    margin-top: 34px; font-size: 20px; font-weight: 500;
    color: var(--brand-red); text-transform: uppercase;
  }
  .person__title {
    margin-top: 2px; font-size: 15px; font-weight: 500;
    color: var(--ink); text-transform: uppercase;
  }
  .address {
    margin-top: 20px; font-size: 14.5px; line-height: 18px; color: var(--ink-soft);
  }
  .contact-list { margin-top: 11px; list-style: none; }
  .contact-list li {
    display: flex; justify-content: flex-end; align-items: center;
    font-size: 14.5px; line-height: 19px; color: var(--ink-soft);
  }
  .contact-list svg { width: 13px; height: 13px; margin-left: 8px; fill: var(--brand-red); }

  .back__mark {
    position: absolute; left: 240px; top: 68px; width: 120px; height: 120px;
    background: var(--brand-red);
  }
  .back__name {
    position: absolute; left: 0; right: 0; top: 228px; text-align: center;
    font-size: 27px; font-weight: 500; color: var(--ink); letter-spacing: 0.5px;
  }
  .back__web {
    position: absolute; left: 0; right: 0; top: 292px; text-align: center;
    font-size: 14px; color: var(--ink-soft); letter-spacing: 5px;
  }
</style>
</head>
<body>
<main class="canvas">
  <section class="card card--front">
    <div class="front__band"></div>
    <div class="front__details">
      <p class="company-name">Brindle Auto Ltd.</p>
      <p class="person__name">Mara Ellison</p>
      <p class="person__title">CEO/Founder</p>
      <p class="address">4210 Alder Court<br>Fairbanks, Alaska 34590</p>
      <ul class="contact-list">
        <li>555 201 4817
          <svg viewBox="0 0 16 16" aria-hidden="true"><path d="M3.5 1l2.5 3-1.5 1.8c.9 2 2.4 3.5 4.4 4.4L10.7 8.7l3 2.5-1.4 2.8C7 13.5 2.5 9 2 3.2z"/></svg></li>
        <li>555 730 2264
          <svg viewBox="0 0 16 16" aria-hidden="true"><path d="M4 0h8v16H4zM5.5 2v10h5V2zM7 13.2h2v1.3H7z" fill-rule="evenodd"/></svg></li>
        <li>555 418 9053
          <svg viewBox="0 0 16 16" aria-hidden="true"><path d="M4 1h8v4H4zM1 6h14v6h-3v3H4v-3H1zM5.5 10.5v3h5v-3z" fill-rule="evenodd"/></svg></li>
        <li>mara@brindleauto.com
          <svg viewBox="0 0 16 16" aria-hidden="true"><path d="M1 3h14v10H1zM2.5 5v6.5h11V5L8 9z" fill-rule="evenodd"/></svg></li>
        <li>www.brindleauto.com
          <svg viewBox="0 0 16 16" aria-hidden="true"><circle cx="8" cy="8" r="7"/><path d="M4 5c2 0 2 2 4 2s1 3 3 3" stroke="#f2f2f2" stroke-width="1.4" fill="none"/></svg></li>
      </ul>
    </div>
  </section>

  <section class="card card--back">
    <div class="back__mark"></div>
    <p class="back__name">Brindle Auto Ltd.</p>
    <p class="back__web">www.brindleauto.com</p>
  </section>
</main>
</body>
</html>
```